Property Developer - Simple yet Sophisticated and Sharp Business Card

We are a medium sized property developer involved mainly in townhouse developments and land subdivisions.

The company is looking for a simple, sharp and sophisticated business card that will be given to contractors, land owners, financiers etc and thus will need to look professional.

Property development related graphics and art can be used, however the card is not to be too "busy" or crowded. Our company name is Kestrel Developments which could possibly be incorporated into the graphics or artwork.

Single sided and/or double sided designs will be acceptable.

A Simple, Sophisticated, Sharp design please!

Good Luck !

```html
<!DOCTYPE html>
<html lang="en">
<head>
<meta charset="utf-8">
<title>Kestrel Developments – Business Card</title>
<link rel="stylesheet" href="https://fonts.googleapis.com/css2?family=Arimo:wght@400;700&display=swap">
<style>
  :root {
    --page: #e6e6e6;
    --card-dark: #1f1a17;
    --card-light: #ffffff;
    --wave-grey: #cfcfcf;
    --gold: #e8a93a;
    --ink-light: #ffffff;
    --ink-dark: #1f1a17;
  }
  html, body {
    margin: 0;
    padding: 0;
    width: 1200px;
    height: 951px;
    overflow: hidden;
    background: var(--page);
    font-family: "Arimo", Arial, sans-serif;
  }
  .canvas {
    position: relative;
    width: 1200px;
    height: 951px;
  }
  .card {
    position: absolute;
    width: 540px;
    height: 330px;
    border-radius: 26px;
    overflow: hidden;
    box-shadow: 0 10px 24px rgba(0,0,0,0.25);
  }
  .card-front {
    left: 70px;
    top: 140px;
    background: var(--card-dark);
  }
  .card-back {
    left: 590px;
    top: 470px;
    background: var(--card-light);
  }
  .brand {
    position: absolute;
    display: flex;
    align-items: center;
    gap: 14px;
    font-weight: 700;
    white-space: nowrap;
  }
  .brand-mark {
    width: 22px;
    height: 22px;
    background: var(--gold);
  }
  .card-front .brand {
    left: 50%;
    top: 50%;
    transform: translate(-50%, -50%);
    color: var(--ink-light);
    font-size: 40px;
  }
  .card-back .brand {
    left: 50%;
    top: 78px;
    transform: translateX(-50%);
    color: var(--ink-dark);
    font-size: 32px;
  }
  .card-back .brand-mark {
    width: 18px;
    height: 18px;
  }
  .back-shapes {
    position: absolute;
    inset: 0;
  }
  .contact {
    position: absolute;
    left: 50%;
    top: 208px;
    transform: translateX(-50%);
    text-align: center;
    color: var(--ink-light);
    font-size: 14px;
    line-height: 1.3;
    white-space: nowrap;
  }
  .contact-name {
    color: var(--gold);
    font-size: 18px;
    margin: 0;
  }
  .contact-role {
    margin: 0 0 8px;
    font-size: 15px;
  }
  .contact-line {
    margin: 0;
  }
</style>
</head>
<body>
<main class="canvas">
  <section class="card card-front" aria-label="Business card front">
    <div class="brand"><span class="brand-mark"></span>Kestrel Developments</div>
  </section>

  <section class="card card-back" aria-label="Business card back">
    <svg class="back-shapes" viewBox="0 0 540 330" preserveAspectRatio="none" aria-hidden="true">
      <path d="M0 170 C 140 150, 300 215, 540 175 L540 330 L0 330 Z" fill="var(--wave-grey)"/>
      <path d="M0 188 C 140 168, 300 230, 540 190 L540 330 L0 330 Z" fill="var(--card-dark)"/>
    </svg>
    <div class="brand"><span class="brand-mark"></span>Kestrel Developments</div>
    <div class="contact">
      <p class="contact-name">Liam Hartley</p>
      <p class="contact-role">Administration</p>
      <p class="contact-line">P: (07) 3000 1842 &nbsp;F: (07) 3000 1843</p>
      <p class="contact-line">E: projects@kestreldevelopments.com.au</p>
      <p class="contact-line">PO Box 2741 Marlow Heights QLD 4120</p>
    </div>
  </section>
</main>
</body>
</html>
```